Business Card for Coastal Tundrabridge Advisory

We need a business card for Coastal Tundrabridge Advisory. The company website address is provided below. The company logo is attached. We provide specialized permafrost services to the mining, transportation, and oil & gas industries. The card should be prepared for:
Matthias Korhonen, PhD.
Coastal Tundrabridge Advisory
PO Box 418259
Quillwater, Alaska 99642
Direct: +1-907-555-0143
Email: mkorhonen@tundrabridgeadvisory.example
Website: www.coastaltundrabridgeadvisory.example

```html
<!DOCTYPE html>
<html lang="en">
<head>
<meta charset="utf-8">
<title>Coastal Tundrabridge Advisory – Business Card</title>
<link rel="stylesheet" href="https://fonts.googleapis.com/css2?family=Open+Sans:ital,wdth,wght@0,75..100,300..800;1,75..100,300..800&display=swap">
<style>
  :root {
    --backdrop: #ececec;
    --card-white: #ffffff;
    --panel-grey: #808080;
    --card-dark: #3b3b3b;
    --ink: #1c1c1c;
    --wordmark: #141414;
    --on-panel: #ffffff;
  }
  * { margin: 0; padding: 0; box-sizing: border-box; }
  html, body {
    width: 1200px;
    height: 1199px;
    overflow: hidden;
    background: var(--backdrop);
    font-family: "Open Sans", Arial, sans-serif;
  }
  .card {
    position: absolute;
    left: 235px;
    width: 726px;
    height: 411px;
    border-radius: 28px;
    overflow: hidden;
  }
  .card--front { top: 156px; background: var(--card-white); }
  .card--back { top: 650px; background: var(--card-dark); }

  .contact-panel {
    position: absolute;
    left: 0; top: 0;
    width: 726px; height: 411px;
  }
  .contact-list {
    position: absolute;
    left: 64px;
    top: 123px;
    list-style: none;
    color: var(--on-panel);
    font-weight: 700;
    font-stretch: 80%;
    font-size: 14.5px;
    line-height: 26.7px;
  }
  .contact-list li { display: flex; align-items: center; gap: 7px; }
  .contact-list svg { width: 17px; height: 17px; flex: none; }
  .postal {
    position: absolute;
    left: 62px;
    top: 246px;
    color: var(--on-panel);
    font-weight: 700;
    font-stretch: 80%;
    font-size: 14.5px;
    line-height: 20px;
    font-style: normal;
  }
  .holder {
    position: absolute;
    right: 42px;
    top: 170px;
    text-align: right;
    color: var(--ink);
    font-style: italic;
    font-weight: 700;
    font-stretch: 80%;
  }
  .holder__name { font-size: 18.5px; line-height: 24px; letter-spacing: -0.2px; }
  .holder__role { font-size: 9px; line-height: 12px; }
  .holder__rule {
    width: 84px; height: 3px;
    background: var(--ink);
    margin: 11px 19px 0 auto;
    border-radius: 2px;
  }

  .wordmark {
    position: absolute;
    left: 0; right: 0;
    top: 190px;
    text-align: center;
    color: var(--wordmark);
    font-weight: 600;
    font-size: 27px;
    letter-spacing: 4px;
    text-transform: uppercase;
  }
</style>
</head>
<body>
  <section class="card card--front" aria-label="Card front">
    <svg class="contact-panel" viewBox="0 0 726 411" aria-hidden="true">
      <path d="M0 61 H312 Q322 61 327 70 L396 198 Q400 207 396 216 L327 345 Q322 354 312 354 H0 Z" fill="var(--panel-grey)"/>
    </svg>
    <ul class="contact-list">
      <li>
        <svg viewBox="0 0 20 20" fill="none" stroke="#fff" stroke-width="1.4"><circle cx="10" cy="10" r="8.8"/><path d="M7 5.5 L8.5 8 L7.6 9 Q8.8 11.5 11 12.4 L12 11.5 L14.5 13 Q14 15 12 14.6 Q6.5 13 5.4 7.8 Q5.2 5.8 7 5.5Z" fill="#fff" stroke="none"/></svg>
        <span>+1-907-555-0143</span>
      </li>
      <li>
        <svg viewBox="0 0 20 20" fill="none" stroke="#fff" stroke-width="1.4"><circle cx="10" cy="10" r="8.8"/><rect x="7.3" y="5" width="5.4" height="10" rx="1"/></svg>
        <span>(907) 555 0143</span>
      </li>
      <li>
        <svg viewBox="0 0 20 20" fill="none" stroke="#fff" stroke-width="1.4"><circle cx="10" cy="10" r="8.8"/><rect x="5.5" y="7" width="9" height="6.4" fill="#fff" stroke="none"/><path d="M5.5 7 L10 10.5 L14.5 7" stroke="var(--panel-grey)" stroke-width="1"/></svg>
        <span>mkorhonen@tundrabridgeadvisory.example</span>
      </li>
      <li>
        <svg viewBox="0 0 20 20" fill="none" stroke="#fff" stroke-width="1.4"><circle cx="10" cy="10" r="8.8"/><circle cx="10" cy="10" r="5"/><path d="M5 10 H15 M10 5 Q7 10 10 15 M10 5 Q13 10 10 15"/></svg>
        <span>www.coastaltundrabridgeadvisory.example</span>
      </li>
    </ul>
    <address class="postal">
      PO Box 418259<br>
      Quillwater, Alaska 99642
    </address>
    <div class="holder">
      <p class="holder__name">Matthias Korhonen, PhD</p>
      <p class="holder__role">Founder &amp; Director</p>
      <div class="holder__rule"></div>
    </div>
  </section>

  <section class="card card--back" aria-label="Card back">
    <p class="wordmark">Coastal Tundrabridge Advisory</p>
  </section>
</body>
</html>
```